BrindleStaffing Business Card Design

We are a staffing company finding positions for dedicated nurses and physicians.

Target Market(s)

Business Professionals

Industry/Entity Type

Staffing

Contact Information for Business Card

Gordon Pratley
Chairman
417 39th Avenue South
SAINT PETERSBURG FL 33712
813-555-4172 Mobile
813-555-8036 Fax
gpratley@brindlestaffing.com
www.brindlestaffing.com

Font styles to use
Sans Serif

Colors
fbee3e
f04a50
f37122

Requirements
Must have
• Logo Attached, see colors below. We'd like to see Yellow, Orange and Red.

```html
<!DOCTYPE html>
<html lang="en">
<head>
<meta charset="utf-8">
<title>BrindleStaffing Business Card</title>
<link rel="stylesheet" href="https://fonts.googleapis.com/css2?family=Roboto:wght@400;500;700&display=swap">
<style>
  :root {
    --stage: #2b2b2b;
    --brand-yellow: #fbee3e;
    --brand-orange: #f37122;
    --brand-red: #f04a50;
    --paper: #ffffff;
    --ink: #3f3f3f;
    --on-color: #ffffff;
  }
  * { margin: 0; padding: 0; box-sizing: border-box; }
  html, body {
    width: 1200px;
    height: 768px;
    overflow: hidden;
    background: var(--stage);
    font-family: "Roboto", Arial, sans-serif;
  }
  .stage {
    position: relative;
    width: 1200px;
    height: 768px;
    display: flex;
    align-items: center;
    justify-content: center;
    gap: 40px;
  }
  .card {
    position: relative;
    width: 540px;
    height: 309px;
    border-radius: 18px;
    overflow: hidden;
  }

  /* Back side */
  .card-back {
    background: linear-gradient(135deg, var(--brand-orange) 0%, var(--brand-red) 100%);
  }
  .card-back .texture {
    position: absolute;
    inset: 0;
    background: radial-gradient(circle at 50% 45%, rgba(251, 238, 62, 0.35) 0%, rgba(251, 238, 62, 0) 65%);
  }
  .card-back .wordmark {
    position: absolute;
    left: 0;
    right: 0;
    top: 116px;
    display: flex;
    align-items: center;
    justify-content: center;
    gap: 10px;
    color: var(--on-color);
    font-weight: 700;
    font-size: 40px;
    letter-spacing: 0.5px;
  }
  .card-back .wordmark .dot {
    width: 12px;
    height: 12px;
    border-radius: 50%;
    background: var(--brand-yellow);
  }
  .card-back .web {
    position: absolute;
    left: 0;
    right: 0;
    bottom: 30px;
    text-align: center;
    color: var(--on-color);
    font-size: 11px;
    letter-spacing: 4px;
  }

  /* Front side */
  .card-front {
    background: var(--paper);
  }
  .card-front .wordmark {
    position: absolute;
    left: 104px;
    top: 44px;
    display: flex;
    align-items: center;
    gap: 8px;
    color: var(--brand-red);
    font-weight: 700;
    font-size: 30px;
  }
  .card-front .wordmark .dot {
    width: 10px;
    height: 10px;
    border-radius: 50%;
    background: var(--brand-orange);
  }
  .contact {
    position: absolute;
    left: 62px;
    top: 128px;
    color: var(--ink);
    font-size: 13.5px;
    line-height: 19px;
  }
  .contact .address { margin-bottom: 10px; }
  .contact .label {
    color: var(--brand-orange);
    font-weight: 500;
  }
  .name-panel {
    position: absolute;
    left: 372px;
    top: -30px;
    width: 400px;
    height: 400px;
    border-radius: 50%;
    background: linear-gradient(160deg, var(--brand-orange) 0%, var(--brand-red) 70%);
  }
  .name-accent {
    position: absolute;
    left: 372px;
    top: -30px;
    width: 400px;
    height: 400px;
    border-radius: 50%;
    border-left: 5px solid var(--brand-yellow);
  }
  .identity {
    position: absolute;
    right: 42px;
    top: 62px;
    height: 200px;
    writing-mode: vertical-rl;
    color: var(--on-color);
    text-align: center;
  }
  .identity .name {
    font-size: 25px;
    font-weight: 500;
  }
  .identity .title {
    font-size: 12.5px;
    margin-right: 4px;
  }
</style>
</head>
<body>
<main class="stage">
  <section class="card card-back" aria-label="Card back">
    <div class="texture" role="img" aria-label="Soft warm dotted background texture"></div>
    <div class="wordmark"><span>BrindleStaffing</span><span class="dot"></span></div>
    <div class="web">www.brindlestaffing.com</div>
  </section>

  <section class="card card-front" aria-label="Card front">
    <div class="wordmark"><span>BrindleStaffing</span><span class="dot"></span></div>
    <div class="contact">
      <p class="address">417 39th Avenue South<br>SAINT PETERSBURG FL 33712</p>
      <p><span class="label">Cell:</span> 813-555-4172</p>
      <p><span class="label">Fax:</span> 813-555-8036</p>
      <p><span class="label">Email:</span> gpratley@brindlestaffing.com</p>
      <p><span class="label">Web:</span> www.brindlestaffing.com</p>
    </div>
    <div class="name-panel"></div>
    <div class="name-accent"></div>
    <div class="identity">
      <span class="name">Gordon Pratley</span>
      <span class="title">Chairman</span>
    </div>
  </section>
</main>
</body>
</html>
```